Vernac Law Business cards and stationary design project

We are looking for a stationary design for business cards (double sided), 8x10, 5x7, and legal and standard envelopes.

We would like the design to match the logo that we have already.
Color palate preferred is Teal, White, grey and any others that will look good for a professional law firm.

We would like this statement: "RELATIONSHIPS. RESPECT. RESULT" to be on the back of the business cards and maybe on the stationary if it looks good.

Please see link to website for more information: www.vernac-law.example

Target Market(s)

Potential clients that need Attorney services.

Industry/Entity Type

Law Firm

Contact Information for Business Card

We would like the front and back to be two different colors. Current business cards are teal front, grey back and are a vertical design. We are open to options with colors.

Font styles to use
Serif

Colors
33a6d7
33b8a4
b9b9b9
5c5c5c

Requirements
Must have
• Logo supplied needs to go on the card and stationary.
• Match website color palate, www.vernac-law.example
• Be professional and not too wordy.
• Criminal Law, Civil Litigation, Personal Injury, Restraining Orders need to be on the card.
Nice to have
• RELATIONSHIPS. RESPECT. RESULTS. on the back of the card.
Should not have
• Not be too busy/wordy or too flashy.

```html
<!DOCTYPE html>
<html lang="en">
<head>
<meta charset="utf-8">
<title>Vernac Law Business Cards</title>
<link href="https://fonts.googleapis.com/css2?family=Libre+Baskerville:wght@400;700&display=swap" rel="stylesheet">
<style>
  :root {
    --teal: #138a9e;
    --white: #ffffff;
    --grey-dark: #5c5c5c;
    --grey-light: #b9b9b9;
    --backdrop: #2b2b2d;
  }
  * { margin: 0; padding: 0; box-sizing: border-box; }
  html, body {
    width: 1200px; height: 900px; overflow: hidden;
    background: var(--backdrop);
    font-family: "Libre Baskerville", Georgia, serif;
  }
  .canvas { position: relative; width: 1200px; height: 900px; }

  .card {
    position: absolute;
    width: 620px; height: 360px;
    border-radius: 24px;
    overflow: hidden;
  }

  /* Back card */
  .card-back {
    left: 60px; top: 60px;
    background: var(--teal);
    color: var(--white);
  }
  .card-back .firm-name {
    position: absolute; left: 56px; top: 118px;
    display: flex; align-items: center; gap: 14px;
    font-size: 34px; font-weight: 400; letter-spacing: 2px;
    text-transform: uppercase; white-space: nowrap;
  }
  .firm-dot {
    width: 14px; height: 14px; border-radius: 50%;
    background: currentColor; flex: none;
  }
  .card-back .footer {
    position: absolute; right: 40px; bottom: 52px;
    text-align: right; white-space: nowrap;
  }
  .card-back .website {
    font-size: 15px; letter-spacing: 5px; margin-bottom: 8px;
  }
  .card-back .tagline {
    font-size: 14px; letter-spacing: 1px;
  }

  /* Front card */
  .card-front {
    left: 520px; top: 480px;
    background: var(--white);
    color: var(--grey-dark);
  }
  .card-front .edge-tab {
    position: absolute; left: 0; top: 88px;
    width: 30px; height: 130px;
    background: var(--teal);
    border-radius: 0 28px 28px 0;
  }
  .card-front .person {
    position: absolute; left: 50px; top: 88px;
    white-space: nowrap;
  }
  .person-name {
    font-size: 21px; font-weight: 700; letter-spacing: 1px;
  }
  .person-name .surname { color: var(--teal); }
  .person-role {
    color: var(--teal); font-size: 14px; margin: 4px 0 10px;
  }
  .contact-list { list-style: none; font-size: 14px; line-height: 1.5; }
  .contact-list li { display: flex; align-items: center; gap: 8px; }
  .contact-list svg { width: 11px; height: 11px; flex: none; }

  .card-front .firm-name {
    position: absolute; left: 350px; top: 118px;
    display: flex; align-items: center; gap: 12px;
    color: var(--teal);
    font-size: 30px; font-weight: 400; letter-spacing: 1px;
    white-space: nowrap;
  }
  .card-front .address {
    position: absolute; right: 40px; bottom: 56px;
    text-align: right; font-size: 14px; line-height: 1.6;
    font-style: normal; white-space: nowrap;
  }
</style>
</head>
<body>
<div class="canvas">

  <section class="card card-back">
    <div class="firm-name"><span class="firm-dot"></span>Vernac Law</div>
    <div class="footer">
      <p class="website">www.vernac-law.example</p>
      <p class="tagline">RELATIONSHIPS. RESPECT. RESULT</p>
    </div>
  </section>

  <section class="card card-front">
    <div class="edge-tab"></div>
    <div class="person">
      <p class="person-name">CLAIRE <span class="surname">VERNAC</span></p>
      <p class="person-role">Lawyer</p>
      <ul class="contact-list">
        <li>
          <svg viewBox="0 0 12 12"><path d="M2.5 1 L4.5 1 L5.2 3.6 L4 4.6 Q5 7 7.4 8 L8.4 6.8 L11 7.5 L11 9.5 Q10.5 11 9 11 Q1 10 1 3 Q1 1.5 2.5 1 Z" fill="var(--teal)"/></svg>
          (555) 014-2870
        </li>
        <li>
          <svg viewBox="0 0 12 12"><rect x="1" y="2.5" width="10" height="7" fill="none" stroke="var(--teal)" stroke-width="1.2"/><path d="M1 2.5 L6 6.5 L11 2.5" fill="none" stroke="var(--teal)" stroke-width="1.2"/></svg>
          claire@vernac-law.example
        </li>
        <li>
          <svg viewBox="0 0 12 12"><circle cx="6" cy="6" r="5" fill="none" stroke="var(--teal)" stroke-width="1.1"/><ellipse cx="6" cy="6" rx="2.2" ry="5" fill="none" stroke="var(--teal)" stroke-width="1"/><path d="M1 6 H11" stroke="var(--teal)" stroke-width="1"/></svg>
          www.vernac-law.example
        </li>
      </ul>
    </div>
    <div class="firm-name"><span class="firm-dot"></span>Vernac Law</div>
    <address class="address">
      4180 Harbor View Blvd.<br>
      #210 Seacliff Bay, CA 90000
    </address>
  </section>

</div>
</body>
</html>
```